Website Quibrel Outdoor

Hi I'm looking for a simple design for a new website. It's outdoor products mainly in category, Boat, Tarpaulin, Fishing, Golf. I have include image and text for 8 products + presentation etc. I want a simple and modern site + fast + Mobile. Wordpress. I'm going to sell through Tradovik so I don't need any WooCommerce but a buy button to Tradovik. I haven set up the Tradovik account yet. My logo i s grey and orange. My goal is to sell in Tradovik US and later EU.

```html
<!DOCTYPE html>
<html lang="en">
<head>
<meta charset="utf-8">
<title>Quibrel Outdoor</title>
<link href="https://fonts.googleapis.com/css2?family=Fjalla+One&family=Fira+Sans+Condensed:wght@400;500&display=swap" rel="stylesheet">
<style>
:root{
  --orange:#f07a1a;
  --orange-deep:#e86f10;
  --ink:#333333;
  --muted:#666666;
  --footer:#2e2b2b;
  --white:#ffffff;
  --line:#e9a35f;
}
*{box-sizing:border-box;margin:0;padding:0}
html,body{width:1200px;height:3176px;overflow:hidden;background:var(--white)}
body{position:relative;font-family:"Fira Sans Condensed",sans-serif;color:var(--ink)}
.abs{position:absolute}
.heading{font-family:"Fjalla One",sans-serif;font-weight:400}
.section-title{position:absolute;left:0;width:1200px;text-align:center;font-family:"Fjalla One",sans-serif;color:var(--orange);font-size:38px;letter-spacing:0.5px}
.btn{position:absolute;background:var(--orange);color:var(--white);font-family:"Fjalla One",sans-serif;font-size:14px;display:flex;align-items:center;justify-content:center}

/* hero */
.hero{left:0;top:0;width:1200px;height:600px;background:radial-gradient(ellipse at 78% 72%,#d9661a 0%,#7a3b17 22%,#3b3326 48%,#2b3a2a 75%,#1f2b24 100%)}
.brand{left:118px;top:64px;display:flex;align-items:center;gap:10px;color:var(--orange);font-family:"Fjalla One",sans-serif;font-size:30px;letter-spacing:1px}
.brand .dot{width:22px;height:22px;border-radius:50%;background:var(--orange)}
.nav{top:74px;left:634px;display:flex;gap:40px;font-family:"Fjalla One",sans-serif;color:var(--white);font-size:13px;letter-spacing:0.2px}
.hero-title{left:0;top:268px;width:1260px;text-align:center;color:var(--white);font-family:"Fjalla One",sans-serif;font-size:48px;text-shadow:0 2px 4px rgba(0,0,0,.35)}
.hero-btn{left:534px;top:342px;width:132px;height:46px;font-size:13px}

/* services */
.service{position:absolute;top:766px;width:240px;text-align:center}
.service .photo{width:152px;height:152px;border-radius:50%;margin:0 auto}
.service h3{font-family:"Fjalla One",sans-serif;color:var(--orange);font-size:18px;font-weight:400;margin-top:10px}
.service p{font-size:11px;line-height:26px;color:var(--muted);margin-top:6px}
.service .btn{position:relative;margin:18px auto 0;width:117px;height:40px}

/* about */
.about{left:0;top:1194px;width:1200px;height:420px;background:linear-gradient(100deg,#b8822c 0%,#c98a2a 30%,#de7a22 55%,#b98030 80%,#9a7a35 100%)}
.about h2{position:absolute;left:111px;top:68px;color:var(--white);font-family:"Fjalla One",sans-serif;font-size:38px;line-height:50px;font-weight:400}
.about p{position:absolute;left:111px;top:180px;width:400px;color:var(--white);font-size:14.5px;line-height:25px}
.about .btn-light{position:absolute;left:115px;top:310px;width:116px;height:41px;background:var(--white);color:var(--orange);font-family:"Fjalla One",sans-serif;font-size:14px;display:flex;align-items:center;justify-content:center}
.photo-back{left:605px;top:22px;width:379px;height:377px;background:linear-gradient(160deg,#2c4a6a,#7c8ea0 55%,#cfd4d8)}
.photo-front{left:746px;top:51px;width:318px;height:318px;background:linear-gradient(150deg,#c9ccd0,#9aa1a8 45%,#3b3d3f 80%,#8a7a62)}

/* products */
.card{position:absolute;top:1777px;width:233px;height:455px;border:1px solid var(--line);text-align:center}
.card .photo{margin:27px 0 0 4px;width:227px;height:274px}
.card .cat{font-family:"Fjalla One",sans-serif;font-size:15px;color:#777;margin-top:42px}
.card .name{font-family:"Fjalla One",sans-serif;font-size:18px;color:var(--orange);margin-top:4px}
.card .price{font-family:"Fjalla One",sans-serif;font-size:18px;color:#555;margin-top:6px}

/* news */
.news{position:absolute;top:2402px;width:314px}
.news .photo{width:314px;height:207px}
.news p{font-size:12px;line-height:26px;margin-top:10px;color:var(--ink)}
.news .date{display:flex;align-items:center;gap:6px;font-size:11px;margin-top:8px}
.news .date b{color:var(--orange);font-weight:500}

/* footer */
.footer{left:0;top:2778px;width:1200px;height:398px;background:var(--footer);color:var(--white)}
.footer h4{position:absolute;font-family:"Fjalla One",sans-serif;font-weight:400;font-size:18px}
.footer p{position:absolute;font-size:11.5px;line-height:26px}
.subscribe{position:absolute;left:115px;top:232px;width:257px;height:49px;border:1px solid #4a4646;display:flex}
.subscribe span{flex:1;font-size:11px;display:flex;align-items:center;padding-left:10px}
.subscribe i{width:52px;background:#1c1a1a;display:flex;align-items:center;justify-content:center}
.thumb{position:absolute;top:230px;width:57px;height:51px}
.footer-brand{position:absolute;left:800px;top:172px;display:flex;align-items:center;gap:12px;color:var(--orange);font-family:"Fjalla One",sans-serif;font-size:40px;letter-spacing:1px}
.footer-brand .dot{width:34px;height:34px;border-radius:50%;background:var(--orange)}
.footer-rule{position:absolute;left:115px;top:321px;width:974px;height:1px;background:#8a8585}
.footer-nav{position:absolute;left:116px;top:350px;display:flex;gap:38px;font-family:"Fjalla One",sans-serif;font-size:13px}
</style>
</head>
<body>

<header class="abs hero" role="img" aria-label="Couple pouring coffee beside a tent and a campfire on grass">
</header>
<div class="abs brand"><span class="dot"></span>QUIBREL OUTDOOR</div>
<nav class="abs nav"><span>HOME</span><span>ABOUT US</span><span>GALLERY</span><span>LATEST NEWS</span><span>CONTACT US</span></nav>
<h1 class="abs hero-title">WELCOME TO OUR QUIBREL OUTDOOR</h1>
<div class="btn hero-btn">READ MORE</div>

<h2 class="section-title" style="top:678px">OUR SERVICES</h2>
<div class="service" style="left:106px">
  <div class="photo" role="img" aria-label="Boats stored under white covers" style="background:linear-gradient(160deg,#9fb3c8,#dfe4ea 45%,#4b5562)"></div>
  <h3>Boat</h3>
  <p>Lorem Ipsum is simply dummy text of the printing and typesetting industry. Lorem Ipsum has been the industry's standard dummy text ever since the</p>
  <div class="btn">Read More</div>
</div>
<div class="service" style="left:356px">
  <div class="photo" role="img" aria-label="Hand holding a grey tarpaulin cloth on grass" style="background:radial-gradient(circle at 50% 45%,#9a9a98,#4f7a35 60%,#3c6a2a)"></div>
  <h3>Tarpaulin</h3>
  <p>Lorem Ipsum is simply dummy text of the printing and typesetting industry. Lorem Ipsum has been the industry's standard dummy text ever since the</p>
  <div class="btn">Read More</div>
</div>
<div class="service" style="left:605px">
  <div class="photo" role="img" aria-label="Golf bag on a trolley on green grass" style="background:radial-gradient(circle at 45% 50%,#6a6a6a,#5d8a3a 60%,#4a7a30)"></div>
  <h3>Colf</h3>
  <p>Lorem Ipsum is simply dummy text of the printing and typesetting industry. Lorem Ipsum has been the industry's standard dummy text ever since the</p>
  <div class="btn">Read More</div>
</div>
<div class="service" style="left:854px">
  <div class="photo" role="img" aria-label="Angler in hat and vest holding fishing gear" style="background:radial-gradient(circle at 55% 55%,#7a6a4a,#c9b99a 55%,#f1eee8)"></div>
  <h3>Fishing</h3>
  <p>Lorem Ipsum is simply dummy text of the printing and typesetting industry. Lorem Ipsum has been the industry's standard dummy text ever since the</p>
  <div class="btn">Read More</div>
</div>

<section class="abs about" role="img" aria-label="Angler in orange jacket with fishing reel, warm golden background">
  <h2>ABOUT US<br>QUIBREL OUTDOOR</h2>
  <p>Find an adventure, create a hobby that is related to nature in its vert pristiene shape for your goodness. Tempor incididunt ut labore. Et dolore magna aliqua. Quitts ipsum suspendisse ultrices gravida.</p>
  <div class="btn-light">Read More</div>
  <div class="abs photo-back" role="img" aria-label="Boat deck above dark sea water"></div>
  <div class="abs photo-front" role="img" aria-label="Woman stepping onto a boat with an outboard motor"></div>
</section>

<h2 class="section-title" style="top:1691px">FEATURED PRODUCT</h2>
<div class="card" style="left:113px">
  <div class="photo" role="img" aria-label="Sunglasses with lanyard and lens options" style="background:linear-gradient(180deg,#ffffff,#eef0f3 50%,#ffffff)"></div>
  <div class="cat">BACKPACK ACCESSORIES</div><div class="name">Trekking Hat</div><div class="price">$75</div>
</div>
<div class="card" style="left:361px">
  <div class="photo" role="img" aria-label="Clear mesh tarpaulin with blue zip" style="background:linear-gradient(135deg,#2a3440,#c9d6e6 40%,#2a5ad0 60%,#dfe6ef)"></div>
  <div class="cat">BACKPACK ACCESSORIES</div><div class="name">Trekking Hat</div><div class="price">$75</div>
</div>
<div class="card" style="left:609px">
  <div class="photo" role="img" aria-label="Golf bag on trolley on grass" style="background:radial-gradient(circle at 50% 45%,#5a5a5a,#6a9a45 55%,#5a8a3a)"></div>
  <div class="cat">BACKPACK ACCESSORIES</div><div class="name">Trekking Hat</div><div class="price">$75</div>
</div>
<div class="card" style="left:857px">
  <div class="photo" role="img" aria-label="Golf bag with towel hanging on grass" style="background:linear-gradient(160deg,#3a3a3a,#8a8a88 45%,#6a9a45)"></div>
  <div class="cat">BACKPACK ACCESSORIES</div><div class="name">Trekking Hat</div><div class="price">$75</div>
</div>

<h2 class="section-title" style="top:2311px">LATEST NEWS</h2>
<div class="news" style="left:115px">
  <div class="photo" role="img" aria-label="Fisherman tying a line at sunset" style="background:linear-gradient(160deg,#c9a79a,#8a7a7c 50%,#3f3a3e)"></div>
  <p>Lorem Ipsum is simply dummy text of the printing and typesetting industry.</p>
  <div class="date"><svg width="18" height="16" viewBox="0 0 18 16"><rect x="1" y="2" width="16" height="13" fill="#222"/><rect x="3" y="6" width="3" height="2" fill="#fff"/><rect x="7.5" y="6" width="3" height="2" fill="#fff"/><rect x="12" y="6" width="3" height="2" fill="#fff"/><rect x="3" y="10" width="3" height="2" fill="#fff"/><rect x="7.5" y="10" width="3" height="2" fill="#fff"/><rect x="12" y="10" width="3" height="2" fill="#fff"/></svg><span><b>10</b> june March</span></div>
</div>
<div class="news" style="left:443px">
  <div class="photo" role="img" aria-label="Man crouching on a boat deck by the water" style="background:linear-gradient(160deg,#b9bec2,#7d868c 55%,#2c3440)"></div>
  <p>Lorem Ipsum is simply dummy text of the printing and typesetting industry.</p>
  <div class="date"><svg width="18" height="16" viewBox="0 0 18 16"><rect x="1" y="2" width="16" height="13" fill="#222"/><rect x="3" y="6" width="3" height="2" fill="#fff"/><rect x="7.5" y="6" width="3" height="2" fill="#fff"/><rect x="12" y="6" width="3" height="2" fill="#fff"/><rect x="3" y="10" width="3" height="2" fill="#fff"/><rect x="7.5" y="10" width="3" height="2" fill="#fff"/><rect x="12" y="10" width="3" height="2" fill="#fff"/></svg><span><b>10</b> june March</span></div>
</div>
<div class="news" style="left:773px">
  <div class="photo" role="img" aria-label="Angler in hat and vest with fishing rod" style="background:linear-gradient(160deg,#f4efe9,#c9b89a 50%,#6f5f45)"></div>
  <p>Lorem Ipsum is simply dummy text of the printing and typesetting industry.</p>
  <div class="date" style="padding-left:24px"><span><b>10</b> june March</span></div>
</div>

<footer class="abs footer" role="img" aria-label="Dark footer with faint campsite backdrop">
  <h4 style="left:116px;top:38px">QUIBREL OUTDOOR</h4>
  <p style="left:115px;top:80px;width:300px">Lorem Ipsum is simply dummy text of the printing and typesetting industry. Lorem Ipsum has been the industry's standard dummy text ever since the 1500s,</p>
  <h4 style="left:493px;top:34px">LATEST TWEETS</h4>
  <p style="left:495px;top:80px;width:175px">Lorem Ipsum is simply dummy text of the printing and typesetting industry. Lorem Ipsum has been.</p>
  <h4 style="left:115px;top:184px">SUBSCRIBE NEWSLETTER</h4>
  <div class="subscribe"><span>Your Email</span><i><svg width="14" height="11" viewBox="0 0 14 11"><rect x="0.75" y="0.75" width="12.5" height="9.5" fill="none" stroke="#fff" stroke-width="1.3"/><path d="M1 1 L7 6 L13 1" fill="none" stroke="#fff" stroke-width="1.3"/></svg></i></div>
  <h4 style="left:495px;top:184px">OUR GALLERY</h4>
  <div class="thumb" role="img" aria-label="Boat at harbour" style="left:496px;background:linear-gradient(160deg,#8fb0d6,#4a6a8a)"></div>
  <div class="thumb" role="img" aria-label="Boat on turquoise water" style="left:561px;background:linear-gradient(160deg,#2aa6b8,#1a6a7a)"></div>
  <div class="thumb" role="img" aria-label="Golf bag on grass" style="left:626px;background:linear-gradient(160deg,#6a6a6a,#6a9a45)"></div>
  <div class="footer-brand"><span class="dot"></span>QUIBREL OUTDOOR</div>
  <div class="footer-rule"></div>
  <nav class="footer-nav"><span>HOME</span><span>ABOUT US</span><span>GALLERY</span><span>LATEST NEWS</span><span>CONTACT US</span></nav>
</footer>

</body>
</html>
```